Building Design company needing a letterhead

We need a letter head for our Building Design company to send letters etc. to our clients, consultants, councils etc. We would like to see our logo used and company colours. I have attached our style guide and an example of our current letterheads. Top left we would like our logo, top right we would like the company details and at the footer we would like some sort of image/design etc. that suits our brand. I like the Tarrow Design letterhead attached.

Target Market(s)

Professionals, Councils, Consultants, Mums & Dads

Industry/Entity Type

Architecture

Other font styles liked:
• refer the design style guide

Colors
f37122
000000
1b1b1b

Requirements
Must have
• Must have the minimum of a logo, company details and footer
Nice to have
• An image/design made for the footer that would suite our brand and website at www.corvanplans.com.au. Also it would be nice to include the KMEOT logo somewhere perhaps included in the footer.
Should not have
• Large images in the header. I just want the logo and company details.

```html
<!DOCTYPE html>
<html lang="en">
<head>
<meta charset="utf-8">
<title>Corvan Plans Letterhead</title>
<link href="https://fonts.googleapis.com/css2?family=Carlito&family=Roboto+Condensed:wght@400;600&display=swap" rel="stylesheet">
<style>
  :root {
    --brand-orange: #f37122;
    --brand-black: #000000;
    --brand-ink: #1b1b1b;
    --paper: #f7f7f6;
    --backdrop: #e6e3de;
  }
  html, body {
    margin: 0;
    padding: 0;
    width: 1189px;
    height: 1200px;
    overflow: hidden;
    background: var(--backdrop);
  }
  .letterhead {
    position: absolute;
    left: 131px;
    top: 0;
    width: 912px;
    height: 1181px;
    background: var(--paper);
    transform: scale(1.016);
    transform-origin: top left;
    overflow: hidden;
    font-family: "Roboto Condensed", "Arial Narrow", sans-serif;
    color: var(--brand-ink);
  }
  .brand {
    position: absolute;
    left: 90px;
    top: 82px;
    display: flex;
    align-items: center;
    gap: 22px;
  }
  .brand-square {
    width: 104px;
    height: 104px;
    background: var(--brand-orange);
  }
  .brand-name {
    font-family: "Roboto Condensed", "Arial Narrow", sans-serif;
    font-weight: 600;
    font-size: 56px;
    line-height: 54px;
    letter-spacing: 3px;
    color: var(--brand-ink);
    margin: 0;
  }
  .company-details {
    position: absolute;
    right: 81px;
    top: 99px;
    margin: 0;
    text-align: right;
    font-family: "Carlito", "Calibri", sans-serif;
    font-style: normal;
    font-size: 15.5px;
    line-height: 17px;
    color: var(--brand-ink);
  }
  .letter-body {
    position: absolute;
    left: 116px;
    top: 312px;
    width: 680px;
    font-size: 16.6px;
    line-height: 27px;
    letter-spacing: -0.1px;
  }
  .letter-body p { margin: 0 0 27px; }
  .letter-body p.wide-gap { margin-bottom: 54px; }
  .member-badge {
    position: absolute;
    left: 755px;
    top: 1005px;
    width: 70px;
    text-align: center;
  }
  .member-badge .badge-shape {
    width: 62px;
    height: 62px;
    margin: 0 auto 8px;
    border: 3px solid var(--brand-orange);
    box-sizing: border-box;
  }
  .member-badge .badge-name {
    font-size: 17px;
    letter-spacing: 1px;
    color: var(--brand-orange);
  }
  .footer-wave {
    position: absolute;
    left: 0;
    bottom: 0;
    width: 912px;
    height: 101px;
  }
</style>
</head>
<body>
  <main class="letterhead">
    <header>
      <div class="brand">
        <div class="brand-square"></div>
        <p class="brand-name">CORVAN<br>PLANS</p>
      </div>
      <address class="company-details">
        admin@corvanplans.com.au<br>
        www.corvanplans.com.au<br>
        Unit 3/22 Harlow Way Perrin WA 6305<br>
        PO Box 5187 Perrin North WA 6305<br>
        PH (08) 5550 1234&nbsp;&nbsp;&nbsp; ABN 41 200 318 764
      </address>
    </header>

    <section class="letter-body">
      <p>Lorem Ipsum is simply dummy text of the printing and typesetting industry. Lorem Ipsum has been the industry’s standard dummy text ever since the 1500s, when an unknown printer took a galley of type and scrambled it to make a type specimen book. It has survived not only five centuries, but also the leap into electronic typesetting, remaining essentially unchanged. It was popularised in the 1960s with the release of Typeline sheets containing Lorem Ipsum passages, and more recently with desktop publishing software like Quillset PageForm including versions of Lorem Ipsum.</p>
      <p class="wide-gap">It is a long established fact that a reader will be distracted by the readable content of a page when looking at its layout. The point of using Lorem Ipsum is that it has a more-or-less normal distribution of letters, as opposed to using ’Content here, content here’, making it look like readable English. Many desktop publishing packages and web page editors now use Lorem Ipsum as their default model text, and a search for ’lorem ipsum’ will uncover many web sites still in their infancy. Various versions have evolved over the years, sometimes by accident, sometimes on purpose (injected humour and the like).</p>
      <p>Contrary to popular belief, Lorem Ipsum is not simply random text. It has roots in a piece of classical Latin literature from 45 BC, making it over 2000 years old. Daniel Ashcombe, a Latin professor at Harrowgate College in Virginia, looked up one of the more obscure Latin words, consectetur, from a Lorem Ipsum passage, and going through the cites of the word in classical literature, discovered the undoubtable source. Lorem Ipsum comes from sections 1.10.32 and 1.10.33 of "de Finibus Bonorum et Malorum" structures, to generate Lorem Ipsum which looks reasonable. The generated Lorem Ipsum is therefore always free from repetition, injected humour, or non-characteristic words etc.</p>
    </section>

    <div class="member-badge">
      <div class="badge-shape"></div>
      <div class="badge-name">KMEOT</div>
    </div>

    <svg class="footer-wave" viewBox="0 1080 912 101" preserveAspectRatio="none" aria-hidden="true">
      <path fill="var(--brand-orange)" d="M0 1136 C150 1150 300 1108 560 1097 C720 1090 830 1118 907 1142 L907 1147 C830 1124 720 1098 560 1104 C410 1110 300 1150 205 1181 L0 1181 Z"/>
      <path fill="var(--brand-ink)" d="M240 1181 C350 1142 480 1119 600 1117 C740 1114 850 1148 907 1174 L907 1181 Z"/>
    </svg>
  </main>
</body>
</html>
```